Card Design Project

We are looking for a couple card / box designs that will for a new company that is in the bereavement assistance industry.
Our customers are churches, counseling centers and funeral homes.
Once we have these card designs we will need to work with that same artist to help us out with box graphic designs that are similar to the card designs. The box is 12" long x 4" wide x 6" high
We will need more designs in the future so we are looking for an artist for future work.
Our look needs to be professional and solemn.
The front of the card should be quite close to what i am attaching but with some professional touches to it that give it a proper look. We dont want you to stray to far from what i have attached but if you feel you have some good ideas we would be more than happy to see them.
The back of the card we want people to be able to leave the family a note so will need wording such as "leave a message to the family" or "write a memory"
Keep in mind we will need this look to be able to match graphics on the box as well, we kind of need the card design and box design to go together.
Thanks
Just wanted to mention to all designers that although we would like our logo on the card it is something that we need to keep kind of in the background somehow. We cant be seen as trying to push a brand name too much so please keep that in mind. Thanks
Designers, I took the need to see what the design looked like on a box out.
Target Market(s)
Funeral homes, churches, counseling centers
Industry/Entity Type
Industry
Requirements
Must have
- Professional and solemn look
Card need to be 4"wide X 6" high and needs to be portrait
A pin will be attached to the top right part of the card so will need a space there for it.
I was thinking that we would have the pic of the ribbon symbol there so when the pin is off the card there would still be a ribbon pic there. The pins that we will be attaching are ribbon pins similar to what i have on my pdf's
Please keep in mind that we cant really have out logo in a dominant area on the card. We would like to have it subtly in there but not to where it is in your face type of thing.
Nice to have
- Our logo but very small, not to intrusive .
Would like 2 designs, one dark and another light.
Maybe 1 masculine or gender neutral and another feminine
Wording should be the same

```html
<!DOCTYPE html>
<html lang="en">
<head>
<meta charset="utf-8">
<title>Memorial Pin Card – Front and Back</title>
<link rel="stylesheet" href="https://fonts.googleapis.com/css2?family=Cinzel:wght@400;500&display=swap">
<style>
  :root {
    --canvas: #ffffff;
    --card-dark: #1c1c1c;
    --card-dark-mid: #3a3a3a;
    --card-light: #d9d9d9;
    --card-edge: #9a9a9a;
    --ink-light: #f2f2f2;
    --ink-dark: #2a2a2a;
    --accent-yellow: #f2d21b;
    --ribbon-grey: #8f8f8f;
    --dot-line: #8a8a8a;
  }
  * { box-sizing: border-box; margin: 0; padding: 0; }
  html, body { width: 900px; height: 1200px; overflow: hidden; background: var(--canvas); }
  body { position: relative; font-family: "Cinzel", "Times New Roman", serif; }

  .card { position: absolute; top: 28px; width: 371px; height: 555px; overflow: hidden; }

  /* Front */
  .card--front {
    left: 70px;
    background:
      radial-gradient(ellipse at 35% 20%, #4a4a4a 0%, transparent 55%),
      radial-gradient(ellipse at 60% 75%, #3c3c3c 0%, transparent 60%),
      linear-gradient(180deg, var(--card-dark-mid), var(--card-dark));
    border: 1px solid #555;
  }
  .floral-artwork {
    position: absolute; left: 120px; top: 0; width: 251px; height: 555px;
    background:
      radial-gradient(ellipse at 45% 62%, rgba(200,200,200,0.32) 0%, transparent 45%),
      radial-gradient(ellipse at 55% 25%, rgba(200,200,200,0.25) 0%, transparent 50%),
      linear-gradient(180deg, rgba(120,120,120,0.18), rgba(90,90,90,0.12));
  }
  .pin-placeholder { position: absolute; left: 296px; top: 6px; width: 40px; height: 58px; }

  .welcome-panel {
    position: absolute; left: 0; top: 122px; width: 202px; height: 313px;
    background: rgba(10,10,10,0.82);
    border-top: 3px solid var(--accent-yellow);
    border-bottom: 3px solid var(--accent-yellow);
    padding: 10px 6px 0 35px;
    color: var(--ink-light);
    font-size: 12px; line-height: 14.6px; letter-spacing: 0.4px;
  }
  .welcome-panel p { margin-bottom: 14.6px; }
  .welcome-panel .salutation { margin-bottom: 14.6px; }

  .brand-mark { position: absolute; display: flex; flex-direction: column; align-items: center; }
  .brand-mark__square { display: block; }
  .brand-mark__name { text-align: center; line-height: 1.05; margin-top: 4px; }
  .card--front .brand-mark { left: 294px; top: 478px; color: var(--ink-light); }
  .card--front .brand-mark__square { width: 30px; height: 30px; background: #0e0e0e; }
  .card--front .brand-mark__name { font-size: 10.5px; }

  /* Back */
  .card--back { left: 459px; background: var(--card-light); border: 1px solid var(--card-edge); }
  .message-heading {
    position: absolute; top: 90px; width: 100%; text-align: center;
    font-size: 13px; letter-spacing: 0.6px; color: var(--ink-dark);
  }
  .message-lines { position: absolute; left: 46px; top: 152px; width: 281px; list-style: none; }
  .message-lines li { height: 40.2px; border-bottom: 1.5px dotted var(--dot-line); }
  .card--back .brand-mark { left: 145px; top: 458px; color: #111; }
  .card--back .brand-mark__square { width: 52px; height: 52px; background: #8a8a8a; }
  .card--back .brand-mark__name { font-size: 11.5px; font-weight: 500; }
</style>
</head>
<body>
  <section class="card card--front" aria-label="Card front">
    <div class="floral-artwork" role="img" aria-label="Line-drawn white floral bouquet with poppies and blossoms"></div>
    <svg class="pin-placeholder" viewBox="0 0 40 58" role="img" aria-label="Space for the ribbon pin">
      <rect x="6" y="4" width="28" height="50" rx="4" fill="var(--ribbon-grey)"/>
    </svg>
    <div class="welcome-panel">
      <p class="salutation">Dear Friends</p>
      <p>Your support in<br>attending this<br>memorial and<br>celebration of life<br>means so much to us.</p>
      <p>Our loved one has<br>touched you in ways<br>we may not even<br>recognize yet.</p>
      <p>We invite you to wear<br>this pin through<br>your grieving process,<br>which we receive<br>as a symbol of your<br>sympathy and support<br>of our loss.</p>
    </div>
    <div class="brand-mark">
      <span class="brand-mark__square"></span>
      <span class="brand-mark__name">Held in<br>Memory</span>
    </div>
  </section>

  <section class="card card--back" aria-label="Card back">
    <h2 class="message-heading">Leave a message to the family</h2>
    <ul class="message-lines">
      <li></li><li></li><li></li><li></li><li></li><li></li><li></li>
    </ul>
    <div class="brand-mark">
      <span class="brand-mark__square"></span>
      <span class="brand-mark__name">Held in<br>Memory</span>
    </div>
  </section>
</body>
</html>
```